Modern looking signage for dental office.

Exterior signage for passing cars
Updates
Need extra days to review
Target Market(s)
Cars passing by
Font styles to use
Sans Serif
Colors
3276b5
Requirements
Must have
- Logo
- OPEN ON SUTURDAY AND SUNDAY
- NIGHT CLINIC AVAILABLE
- PLEASE USE THE FONT TYPE IN FILE 4 UPLOADED BELOW.
- (847) 302-7469
- Modern looking

```html
<!DOCTYPE html>
<html lang="en">
<head>
<meta charset="utf-8">
<title>Nova Dental – Weekend and Night Clinic Sign</title>
<link rel="stylesheet" href="https://fonts.googleapis.com/css2?family=Montserrat:wght@300;800;900&family=Roboto+Condensed:wght@400&display=swap">
<style>
  :root {
    --backdrop: #8c8c8c;
    --sign-white: #ffffff;
    --sign-fade: #ececec;
    --ink: #000000;
    --brand-gray: #3f3b3a;
    --brand-blue: #3276b5;
    --rule-gray: #9a9a9a;
  }
  * { margin: 0; padding: 0; box-sizing: border-box; }
  html, body {
    width: 1200px; height: 1000px; overflow: hidden;
    background: var(--backdrop);
  }
  .canvas { position: relative; width: 1200px; height: 1000px; }
  .sign {
    position: absolute; left: 175px; top: 52px; width: 850px; height: 851px;
    background: linear-gradient(180deg, var(--sign-white) 0%, var(--sign-white) 30%, var(--sign-fade) 100%);
  }
  .sign-frame {
    position: absolute; left: 15px; top: 15px; right: 15px; bottom: 15px;
    border: 2px solid var(--ink);
  }
  .brand-mark {
    position: absolute; left: 80px; top: 58px; width: 144px; height: 144px;
    border: 2px solid var(--brand-gray); border-radius: 50%;
  }
  .brand-name {
    position: absolute; left: 250px; top: 72px;
    font-family: "Montserrat", sans-serif; font-weight: 300;
    font-size: 72px; line-height: 1; letter-spacing: -1px;
    color: var(--brand-gray); white-space: nowrap;
  }
  .brand-tagline {
    position: absolute; left: 295px; top: 170px;
    font-family: "Roboto Condensed", sans-serif; font-weight: 400;
    font-size: 33px; line-height: 1; color: var(--brand-gray);
    white-space: nowrap;
  }
  .tooth-icon {
    position: absolute; left: 70px; top: 290px; width: 82px; height: 100px;
    background: var(--sign-fade); border-radius: 30px 30px 18px 18px;
  }
  .headline {
    position: absolute; font-family: "Montserrat", sans-serif; font-weight: 900;
    color: var(--ink); line-height: 1; white-space: nowrap;
  }
  .headline-open { left: 168px; top: 280px; font-size: 112px; }
  .headline-night { left: 62px; top: 503px; width: 720px; text-align: center; font-size: 100px; }
  .band {
    position: absolute; left: 45px; width: 758px; background: var(--ink);
    color: var(--sign-white); font-family: "Montserrat", sans-serif; font-weight: 800;
    display: flex; align-items: center; justify-content: center;
    white-space: nowrap; line-height: 1;
  }
  .band-days { top: 395px; height: 75px; font-size: 54px; }
  .band-available { top: 606px; height: 73px; font-size: 64px; }
  .divider {
    position: absolute; left: 180px; top: 491px; width: 490px; height: 2px;
    background: var(--rule-gray);
  }
  .phone-icon { position: absolute; left: 52px; top: 730px; width: 82px; height: 82px; }
  .phone-number {
    position: absolute; left: 158px; top: 722px;
    font-family: "Montserrat", sans-serif; font-weight: 900;
    font-size: 92px; line-height: 1; color: var(--ink); white-space: nowrap;
  }
</style>
</head>
<body>
<div class="canvas">
  <div class="sign">
    <div class="sign-frame"></div>

    <div class="brand-mark"></div>
    <div class="brand-name">NOVA DENTAL</div>
    <div class="brand-tagline">MODERN GENERAL DENTISTRY</div>

    <div class="tooth-icon" role="img" aria-label="Tooth outline icon"></div>
    <div class="headline headline-open">OPEN ON</div>
    <div class="band band-days">SATURDAY AND SUNDAY</div>

    <div class="divider"></div>

    <div class="headline headline-night">NIGHT CLINIC</div>
    <div class="band band-available">AVAILABLE</div>

    <svg class="phone-icon" viewBox="0 0 82 82" role="img" aria-label="Phone">
      <circle cx="41" cy="41" r="37" fill="none" stroke="#000" stroke-width="7"/>
      <path d="M27 24 l7 -2 l5 10 l-4 4 c2 5 6 9 11 11 l4 -4 l10 5 l-2 7 c-18 2 -33 -13 -31 -31 z" fill="#000"/>
      <path d="M45 26 a11 11 0 0 1 11 11" fill="none" stroke="#000" stroke-width="3"/>
      <path d="M46 19 a18 18 0 0 1 17 17" fill="none" stroke="#000" stroke-width="3"/>
    </svg>
    <div class="phone-number">847 302 7469</div>
  </div>
</div>
</body>
</html>
```